Rollers & Glides.com

Vertical Business Card with focus on branding with our icon. Information on card will be logo, persons name, position, phone number, email address and website. Use the the name Marcus Pellow, position President, phone number 480.915.2267, email Marcus@rollersandglides-demo.com, website www.rollersandglides-demo.com.

```html
<!DOCTYPE html>
<html lang="en">
<head>
<meta charset="utf-8">
<title>Rollers &amp; Glides.com – Business Card</title>
<link rel="stylesheet" href="https://fonts.googleapis.com/css2?family=Roboto+Condensed:wght@400;500&family=Roboto:wght@400;500&display=swap">
<style>
  :root {
    --backdrop: #d3d1cc;
    --brand-blue: #1a43a3;
    --brand-blue-deep: #14398f;
    --silver: #c9ccd3;
    --paper: #ffffff;
    --ink: #3a3a3a;
    --ink-soft: #555555;
    --rule: #2c2c2c;
  }
  * { margin: 0; padding: 0; box-sizing: border-box; }
  html, body {
    width: 1200px;
    height: 903px;
    overflow: hidden;
    background: var(--backdrop);
  }
  .stage {
    position: relative;
    width: 1200px;
    height: 903px;
  }
  .card {
    position: absolute;
    top: 303px;
    width: 520px;
    height: 297px;
    box-shadow: 0 6px 18px rgba(0,0,0,0.18);
  }
  .card--front {
    left: 50px;
    background: var(--brand-blue);
  }
  .card--back {
    left: 630px;
    background: var(--paper);
  }

  /* Front: brand lockup */
  .front-lockup {
    position: absolute;
    left: 70px;
    top: 128px;
    display: flex;
    align-items: center;
    gap: 16px;
  }
  .front-lockup__dot {
    width: 40px;
    height: 40px;
    border-radius: 50%;
    background: var(--silver);
  }
  .front-lockup__name {
    font-family: "Roboto Condensed", sans-serif;
    font-weight: 500;
    font-size: 30px;
    letter-spacing: 0.5px;
    color: var(--silver);
  }

  /* Back: brand mark area */
  .back-lockup {
    position: absolute;
    left: 36px;
    top: 122px;
    display: flex;
    align-items: center;
    gap: 10px;
  }
  .back-lockup__dot {
    width: 26px;
    height: 26px;
    border-radius: 50%;
    background: var(--brand-blue);
  }
  .back-lockup__name {
    font-family: "Roboto", sans-serif;
    font-weight: 500;
    font-size: 18px;
    color: var(--brand-blue);
  }

  /* Back: person block */
  .person {
    position: absolute;
    right: 40px;
    top: 44px;
    text-align: right;
  }
  .person__name {
    font-family: "Roboto", sans-serif;
    font-weight: 500;
    font-size: 21px;
    color: var(--brand-blue);
    line-height: 1.1;
  }
  .person__rule {
    position: absolute;
    left: 188px;
    right: 40px;
    top: 72px;
    height: 1px;
    background: var(--rule);
  }
  .person__title {
    position: absolute;
    right: 40px;
    top: 77px;
    font-family: "Roboto", sans-serif;
    font-size: 14px;
    color: var(--ink-soft);
  }

  /* Back: contact list */
  .contact {
    position: absolute;
    left: 188px;
    top: 192px;
    list-style: none;
    border-top: 1px solid var(--rule);
    padding-top: 10px;
    width: 292px;
  }
  .contact__item {
    display: flex;
    align-items: center;
    gap: 7px;
    font-family: "Roboto", sans-serif;
    font-size: 13.5px;
    color: var(--ink);
    line-height: 22px;
  }
  .contact__icon {
    width: 12px;
    height: 12px;
    flex: none;
  }
</style>
</head>
<body>
<main class="stage">

  <section class="card card--front" aria-label="Business card front">
    <div class="front-lockup">
      <span class="front-lockup__dot" aria-hidden="true"></span>
      <span class="front-lockup__name">Rollers &amp; Glides.com</span>
    </div>
  </section>

  <section class="card card--back" aria-label="Business card back">
    <div class="person">
      <p class="person__name">Marcus Pellow</p>
    </div>
    <div class="person__rule" aria-hidden="true"></div>
    <p class="person__title">President</p>

    <div class="back-lockup">
      <span class="back-lockup__dot" aria-hidden="true"></span>
      <span class="back-lockup__name">Rollers &amp; Glides.com</span>
    </div>

    <ul class="contact">
      <li class="contact__item">
        <svg class="contact__icon" viewBox="0 0 12 12" aria-hidden="true">
          <rect width="12" height="12" rx="2" fill="var(--brand-blue)"/>
          <path d="M3 3.2c.4-.4.9-.4 1.2 0l.7.9c.2.3.2.7-.1 1l-.4.4c.4.8 1 1.4 1.8 1.8l.4-.4c.3-.3.7-.3 1-.1l.9.7c.4.3.4.8 0 1.2l-.5.5C6.5 9.5 2.5 5.5 2.5 3.7z" fill="#fff"/>
        </svg>
        480.915.2267
      </li>
      <li class="contact__item">
        <svg class="contact__icon" viewBox="0 0 12 12" aria-hidden="true">
          <rect width="12" height="12" rx="2" fill="var(--brand-blue)"/>
          <rect x="2.5" y="3.5" width="7" height="5" fill="none" stroke="#fff" stroke-width="0.9"/>
          <path d="M2.5 3.5 6 6.5 9.5 3.5" fill="none" stroke="#fff" stroke-width="0.9"/>
        </svg>
        Marcus@rollersandglides-demo.com
      </li>
      <li class="contact__item">
        <svg class="contact__icon" viewBox="0 0 12 12" aria-hidden="true">
          <circle cx="6" cy="6" r="6" fill="var(--brand-blue)"/>
          <circle cx="6" cy="6" r="3.6" fill="none" stroke="#fff" stroke-width="0.8"/>
          <ellipse cx="6" cy="6" rx="1.5" ry="3.6" fill="none" stroke="#fff" stroke-width="0.8"/>
          <line x1="2.4" y1="6" x2="9.6" y2="6" stroke="#fff" stroke-width="0.8"/>
        </svg>
        www.rollersandglides-demo.com
      </li>
    </ul>
  </section>

</main>
</body>
</html>
```